Real Estate Webpage Design

We have an existing website: ferndaleestatecollective.com.au
We focus customised service mainly on Property Management and second-hand property sales.
We are not entirely happy about the current design and layout can stay roughly the same as the back end coding is linked to a CRM system.
We would like to see the design are more reachable to our clients and appearing.
Please check our Website Design Draft for more details.

Industry/Entity Type

Real estate Agency

Number of Pages Required

5+ page

Font styles to use
Sans Serif

Colors

Designer to choose colors to be used in the design.

```html
<!DOCTYPE html>
<html lang="en">
<head>
<meta charset="utf-8">
<title>Ferndale Estate Collective – For Lease</title>
<link href="https://fonts.googleapis.com/css2?family=Poppins:wght@400;500;600&display=swap" rel="stylesheet">
<style>
:root{
  --gold:#EBB847;
  --navy:#172B4A;
  --ink:#1E1E1E;
  --text:#333;
  --muted:#777;
  --line:#E4E6EC;
  --tint:#F7F8FC;
  --cream:#FDF8EE;
  --white:#fff;
}
*{box-sizing:border-box;margin:0;padding:0}
html,body{width:1200px;height:3007px;overflow:hidden}
body{font-family:"Poppins",sans-serif;color:var(--text);background:var(--white);position:relative;font-size:14px}
.abs{position:absolute}
a{color:inherit;text-decoration:none}

/* header */
.site-header{position:absolute;left:0;top:0;width:1200px;height:60px;background:var(--white);z-index:3}
.brand{position:absolute;left:60px;top:0;width:225px;height:75px;background:var(--white);display:flex;align-items:center;gap:10px;padding-left:18px}
.brand-mark{width:30px;height:30px;background:var(--gold)}
.brand-name{font-size:24px;font-weight:500;color:var(--gold);line-height:1}
.brand-name small{display:block;font-size:9px;color:var(--ink);letter-spacing:1px;margin-top:3px}
.main-nav{position:absolute;right:238px;top:24px;display:flex;gap:26px;font-size:14px;color:var(--ink)}
.main-nav .active{color:var(--gold);position:relative}
.main-nav .active::after{content:"";position:absolute;left:0;right:0;top:32px;height:2px;background:var(--gold)}
.btn-add{position:absolute;left:1012px;top:18px;width:128px;height:34px;background:var(--gold);color:var(--white);font-size:14px;display:flex;align-items:center;justify-content:center;border:1px solid #c99a2e}

/* hero */
.hero{position:absolute;left:0;top:60px;width:1200px;height:352px;background:linear-gradient(180deg,#4d5660 0%,#6f737a 45%,#8d8c86 100%)}
.hero h1{position:absolute;left:62px;top:130px;font-size:38px;font-weight:600;color:var(--gold)}
.hero p{position:absolute;left:62px;top:195px;font-size:14px;color:var(--white)}

/* search */
.search{position:absolute;left:60px;top:457px;width:1080px;height:53px;background:var(--white);box-shadow:0 2px 12px rgba(0,0,0,.06);display:flex;align-items:center}
.search .type{width:108px;height:100%;border-right:1px solid var(--line);display:flex;align-items:center;justify-content:space-between;padding:0 12px;font-size:14px;color:var(--ink)}
.search .field{flex:1;padding-left:16px;color:var(--muted);font-size:14px}
.search .go{width:44px;height:44px;margin-right:5px;background:var(--gold);display:flex;align-items:center;justify-content:center}

/* savings */
.save-title{position:absolute;left:0;width:1168px;top:586px;text-align:center;font-size:27px;font-weight:500;color:var(--ink)}
.save-card{position:absolute;top:659px;width:261px;height:132px;background:var(--cream);text-align:center;padding-top:24px}
.save-card .lbl{font-size:13px;color:var(--ink)}
.save-card .amt{font-size:27px;font-weight:500;color:var(--ink);margin:2px 0}
.save-card .sub{font-size:14px;color:var(--ink)}
.save-card .sub b{font-weight:600}
.slider-tip{position:absolute;left:478px;top:821px;width:120px;height:52px;border:1px solid #ccc;background:var(--white);text-align:center;padding-top:6px}
.slider-tip span{display:block;font-size:10px}
.slider-tip strong{font-size:17px;font-weight:500;color:var(--ink)}
.track{position:absolute;left:333px;top:890px;width:524px;height:4px;background:var(--cream)}
.track i{display:block;width:204px;height:4px;background:var(--gold)}
.knob{position:absolute;left:527px;top:882px;width:20px;height:20px;border-radius:50%;border:2px solid var(--gold);background:var(--white)}
.range-end{position:absolute;top:866px;text-align:center;font-size:13px;font-weight:500;color:var(--ink)}
.btn{position:absolute;height:35px;display:flex;align-items:center;justify-content:center;font-size:14px}
.btn-sell{left:475px;top:969px;width:98px;background:var(--gold);color:var(--white);border-left:3px solid #b88a25}
.btn-buy{left:595px;top:969px;width:98px;border:1px solid #ccc;color:var(--ink)}
.call{position:absolute;left:0;width:1168px;top:1026px;text-align:center;font-size:14px;color:var(--ink)}
.call b{color:var(--gold);font-size:17px;font-weight:500;margin-left:6px}

/* listings */
.listings{position:absolute;left:0;top:1126px;width:1200px;height:1237px;background:var(--tint)}
.card{position:absolute;width:517px;height:499px;background:var(--white);box-shadow:0 1px 6px rgba(0,0,0,.05)}
.card .photo{position:absolute;left:13px;top:13px;width:491px;height:286px}
.card .tag{position:absolute;left:31px;top:314px;font-size:13px;color:var(--gold)}
.card h3{position:absolute;left:31px;top:336px;font-size:17px;font-weight:500;color:var(--ink)}
.card .addr{position:absolute;left:29px;top:368px;font-size:14px;display:flex;align-items:center;gap:6px;color:var(--ink)}
.card .feats{position:absolute;left:31px;top:402px;display:flex;gap:18px;font-size:14px;color:var(--ink)}
.card .feats span{display:flex;align-items:center;gap:8px}
.card .foot{position:absolute;left:0;bottom:0;width:100%;height:51px;border-top:1px solid var(--line);display:flex;align-items:center;padding:0 17px}
.avatar{width:31px;height:31px;background:#b7bcc6}
.agent{margin-left:12px;font-size:14px;color:var(--ink);flex:1}
.actions{display:flex;gap:8px}
.pager{position:absolute;top:2273px;left:476px;display:flex;gap:14px}
.pager span{width:38px;height:38px;border:1px solid var(--navy);display:flex;align-items:center;justify-content:center;font-size:16px;font-weight:500;color:var(--ink);background:var(--white)}
.pager .dark{background:var(--navy);border-color:var(--navy)}
.pager .cur{background:var(--gold);border-color:var(--gold);color:var(--white)}

/* cta */
.cta{position:absolute;left:0;top:2447px;width:1200px;height:227px;background:var(--navy);text-align:center}
.cta h2{color:var(--white);font-size:23px;font-weight:500;line-height:37px;margin-top:40px}
.cta .btn-cta{display:inline-flex;margin-top:16px;width:208px;height:35px;align-items:center;justify-content:center;background:var(--gold);color:var(--white);font-size:14px;border:1px solid #c99a2e}

/* footer */
.footer-brand{position:absolute;left:60px;top:2716px;display:flex;align-items:center;gap:10px}
.footer-about{position:absolute;left:61px;top:2782px;width:200px;font-size:13px;line-height:23px;color:var(--ink)}
.fcol h4{font-size:14px;font-weight:500;color:var(--gold);margin-bottom:14px}
.fcol{position:absolute;top:2716px}
.fcol ul{list-style:none;font-size:13px;color:var(--ink);line-height:27.5px}
.contact-row{display:flex;gap:10px;font-size:13px;color:var(--ink);line-height:19px;margin-bottom:12px}
.contact-row b{font-weight:600}
.socials{display:flex;gap:16px}
.socials span{width:38px;height:38px;border-radius:50%;border:1.5px solid var(--gold);display:flex;align-items:center;justify-content:center}
.socials span.on{background:var(--gold)}
.socials i{width:12px;height:12px;background:var(--ink);display:block}
.socials span.on i{background:var(--white)}
.legal{position:absolute;left:0;top:2965px;width:1200px;height:42px;border-top:1px solid var(--line);display:flex;align-items:center;padding:0 61px;font-size:13px;color:var(--ink)}
.legal nav{margin-left:auto;display:flex;gap:26px}
</style>
</head>
<body>

<header class="site-header">
  <div class="brand"><span class="brand-mark"></span><span class="brand-name">Ferndale<small>Estate Collective</small></span></div>
  <nav class="main-nav">
    <a>Home</a><a>About Us</a><a class="active">Leasing</a><a>Buy</a><a>Sell</a><a>Our Team</a><a>Blog</a><a>Contact Us</a>
  </nav>
  <a class="btn-add">Add Properties</a>
</header>

<section class="hero" role="img" aria-label="Two-storey stone and weatherboard family house with dormer windows">
  <h1>For Lease</h1>
  <p>Your local real estate property group</p>
</section>

<div class="search">
  <div class="type">Rent <svg width="12" height="8"><path d="M0 0h12L6 8z" fill="#222"/></svg></div>
  <div class="field">Search by Suburb, Postcode or keyword</div>
  <div class="go"><svg width="20" height="20" fill="none" stroke="#fff" stroke-width="2"><circle cx="8.5" cy="8.5" r="6.5"/><path d="M13.5 13.5L19 19"/></svg></div>
</div>

<h2 class="save-title">See How Much You Can Save</h2>
<div class="save-card" style="left:309px"><div class="lbl">YOU SAVE</div><div class="amt">$74,000</div><div class="sub"><b>Buying</b> With Ferndale</div></div>
<div class="save-card" style="left:599px"><div class="lbl">YOU SAVE</div><div class="amt">$1,41,000</div><div class="sub"><b>Buying</b> With Ferndale</div></div>

<div class="slider-tip"><span>Your Home value</span><strong>$74,000</strong></div>
<div class="range-end" style="left:252px"><svg width="28" height="28" fill="none" stroke="#555" stroke-width="1.5"><path d="M3 14L14 3l11 11M7 11v14h14V11M12 25v-7h4v7"/></svg><br>$50,000</div>
<div class="track"><i></i></div>
<div class="knob"></div>
<div class="range-end" style="left:877px"><svg width="28" height="28" fill="none" stroke="#555" stroke-width="1.5"><path d="M3 14L14 3l11 11M7 11v14h14V11M12 25v-7h4v7"/></svg><br>$2,00,000</div>
<a class="btn btn-sell">Sell House</a>
<a class="btn btn-buy">Buy House</a>
<p class="call">Have question? Call us <b>02 6000 4821</b></p>

<section class="listings">
  <article class="card" style="left:60px;top:56px">
    <div class="photo" role="img" aria-label="Rooftop infinity pool beside apartment tower" style="background:linear-gradient(135deg,#8b8f95,#3f6fb0 55%,#c9d8ea)"></div>
    <span class="tag">For Lease</span><h3>Harwood</h3>
    <div class="addr"><svg width="14" height="18" fill="none" stroke="#EBB847" stroke-width="1.3"><path d="M7 17s6-6 6-10A6 6 0 0 0 1 7c0 4 6 10 6 10z"/><circle cx="7" cy="7" r="2"/></svg>12/40 Kestrel Crescent Harwood</div>
    <div class="feats"><span><svg width="22" height="16" fill="none" stroke="#EBB847" stroke-width="1.3"><path d="M1 15V4h20v11M1 11h20M4 8h6v3M12 8h6v3"/></svg>3</span><span><svg width="22" height="18" fill="none" stroke="#EBB847" stroke-width="1.3"><path d="M1 9h20v3a5 5 0 0 1-5 5H6a5 5 0 0 1-5-5zM5 9V3a2 2 0 0 1 4 0"/></svg>2</span><span><svg width="26" height="14" fill="none" stroke="#EBB847" stroke-width="1.3"><path d="M1 10V7l4-1 4-4h8l5 4 3 1v3zM6 10a2 2 0 1 0 4 0M17 10a2 2 0 1 0 4 0"/></svg>2</span></div>
    <div class="foot"><span class="avatar"></span><span class="agent">Mara Lindqvist</span><span class="actions"><svg width="18" height="18" fill="none" stroke="#333" stroke-width="1.3"><circle cx="9" cy="9" r="7.5"/><path d="M9 4v5l3 2"/></svg><svg width="18" height="18" fill="none" stroke="#333" stroke-width="1.3"><path d="M2 6V2h4M12 2h4v4M16 12v4h-4M6 16H2v-4M2 2l5 5M16 2l-5 5M16 16l-5-5M2 16l5-5"/></svg><svg width="20" height="16" fill="none" stroke="#333" stroke-width="1.3"><rect x="1" y="1" width="18" height="14"/><path d="M1 1l9 8 9-8"/></svg></span></div>
  </article>

  <article class="card" style="left:623px;top:56px">
    <div class="photo" role="img" aria-label="Apartment living room with sofa, rug and balcony doors" style="background:linear-gradient(135deg,#6b6258,#b8ab97 50%,#8a5a34)"></div>
    <span class="tag">For Lease</span><h3>Harwood</h3>
    <div class="addr"><svg width="14" height="18" fill="none" stroke="#EBB847" stroke-width="1.3"><path d="M7 17s6-6 6-10A6 6 0 0 0 1 7c0 4 6 10 6 10z"/><circle cx="7" cy="7" r="2"/></svg>5/7 Banksia Street Harwood</div>
    <div class="feats"><span><svg width="22" height="16" fill="none" stroke="#EBB847" stroke-width="1.3"><path d="M1 15V4h20v11M1 11h20M4 8h6v3M12 8h6v3"/></svg>2</span><span><svg width="22" height="18" fill="none" stroke="#EBB847" stroke-width="1.3"><path d="M1 9h20v3a5 5 0 0 1-5 5H6a5 5 0 0 1-5-5zM5 9V3a2 2 0 0 1 4 0"/></svg>2</span><span><svg width="26" height="14" fill="none" stroke="#EBB847" stroke-width="1.3"><path d="M1 10V7l4-1 4-4h8l5 4 3 1v3zM6 10a2 2 0 1 0 4 0M17 10a2 2 0 1 0 4 0"/></svg>1</span></div>
    <div class="foot"><span class="avatar"></span><span class="agent">Mara Lindqvist</span><span class="actions"><svg width="18" height="18" fill="none" stroke="#333" stroke-width="1.3"><circle cx="9" cy="9" r="7.5"/><path d="M9 4v5l3 2"/></svg><svg width="18" height="18" fill="none" stroke="#333" stroke-width="1.3"><path d="M2 6V2h4M12 2h4v4M16 12v4h-4M6 16H2v-4M2 2l5 5M16 2l-5 5M16 16l-5-5M2 16l5-5"/></svg><svg width="20" height="16" fill="none" stroke="#333" stroke-width="1.3"><rect x="1" y="1" width="18" height="14"/><path d="M1 1l9 8 9-8"/></svg></span></div>
  </article>

  <article class="card" style="left:60px;top:593px">
    <div class="photo" role="img" aria-label="Single-storey brick house with garage and front garden" style="background:linear-gradient(180deg,#7ea6dc,#a58d7b 45%,#6f8f4a 75%,#8a3b2e)"></div>
    <span class="tag">For Lease</span><h3>Harwood</h3>
    <div class="addr"><svg width="14" height="18" fill="none" stroke="#EBB847" stroke-width="1.3"><path d="M7 17s6-6 6-10A6 6 0 0 0 1 7c0 4 6 10 6 10z"/><circle cx="7" cy="7" r="2"/></svg>210/3 Wattlebird Parade Harwood</div>
    <div class="feats"><span><svg width="22" height="16" fill="none" stroke="#EBB847" stroke-width="1.3"><path d="M1 15V4h20v11M1 11h20M4 8h6v3M12 8h6v3"/></svg>3</span><span><svg width="22" height="18" fill="none" stroke="#EBB847" stroke-width="1.3"><path d="M1 9h20v3a5 5 0 0 1-5 5H6a5 5 0 0 1-5-5zM5 9V3a2 2 0 0 1 4 0"/></svg>2</span><span><svg width="26" height="14" fill="none" stroke="#EBB847" stroke-width="1.3"><path d="M1 10V7l4-1 4-4h8l5 4 3 1v3zM6 10a2 2 0 1 0 4 0M17 10a2 2 0 1 0 4 0"/></svg>2</span></div>
    <div class="foot"><span class="avatar"></span><span class="agent">Mara Lindqvist</span><span class="actions"><svg width="18" height="18" fill="none" stroke="#333" stroke-width="1.3"><circle cx="9" cy="9" r="7.5"/><path d="M9 4v5l3 2"/></svg><svg width="18" height="18" fill="none" stroke="#333" stroke-width="1.3"><path d="M2 6V2h4M12 2h4v4M16 12v4h-4M6 16H2v-4M2 2l5 5M16 2l-5 5M16 16l-5-5M2 16l5-5"/></svg><svg width="20" height="16" fill="none" stroke="#333" stroke-width="1.3"><rect x="1" y="1" width="18" height="14"/><path d="M1 1l9 8 9-8"/></svg></span></div>
  </article>

  <article class="card" style="left:623px;top:593px">
    <div class="photo" role="img" aria-label="Modern kitchen with light timber cabinets and dark benchtop" style="background:linear-gradient(135deg,#e7e2d8,#c9b89c 55%,#9a978f)"></div>
    <span class="tag">For Lease</span><h3>Harwood</h3>
    <div class="addr"><svg width="14" height="18" fill="none" stroke="#EBB847" stroke-width="1.3"><path d="M7 17s6-6 6-10A6 6 0 0 0 1 7c0 4 6 10 6 10z"/><circle cx="7" cy="7" r="2"/></svg>14 Coral Fern Street Harwood</div>
    <div class="feats"><span><svg width="22" height="16" fill="none" stroke="#EBB847" stroke-width="1.3"><path d="M1 15V4h20v11M1 11h20M4 8h6v3M12 8h6v3"/></svg>2</span><span><svg width="22" height="18" fill="none" stroke="#EBB847" stroke-width="1.3"><path d="M1 9h20v3a5 5 0 0 1-5 5H6a5 5 0 0 1-5-5zM5 9V3a2 2 0 0 1 4 0"/></svg>2</span><span><svg width="26" height="14" fill="none" stroke="#EBB847" stroke-width="1.3"><path d="M1 10V7l4-1 4-4h8l5 4 3 1v3zM6 10a2 2 0 1 0 4 0M17 10a2 2 0 1 0 4 0"/></svg>1</span></div>
    <div class="foot"><span class="avatar"></span><span class="agent">Mara Lindqvist</span><span class="actions"><svg width="18" height="18" fill="none" stroke="#333" stroke-width="1.3"><circle cx="9" cy="9" r="7.5"/><path d="M9 4v5l3 2"/></svg><svg width="18" height="18" fill="none" stroke="#333" stroke-width="1.3"><path d="M2 6V2h4M12 2h4v4M16 12v4h-4M6 16H2v-4M2 2l5 5M16 2l-5 5M16 16l-5-5M2 16l5-5"/></svg><svg width="20" height="16" fill="none" stroke="#333" stroke-width="1.3"><rect x="1" y="1" width="18" height="14"/><path d="M1 1l9 8 9-8"/></svg></span></div>
  </article>
</section>

<nav class="pager">
  <span class="dark"><svg width="12" height="20" fill="none" stroke="#fff" stroke-width="2"><path d="M10 2L2 10l8 8"/></svg></span>
  <span>1</span><span class="cur">2</span><span>3</span>
  <span class="dark"><svg width="12" height="20" fill="none" stroke="#fff" stroke-width="2"><path d="M2 2l8 8-8 8"/></svg></span>
</nav>

<section class="cta">
  <h2>Contact Us If You Want To Sell Your House Or You<br>Have Other Questions</h2>
  <a class="btn-cta">Request Free Consultation</a>
</section>

<footer>
  <div class="footer-brand"><span class="brand-mark"></span><span class="brand-name" style="font-size:30px">Ferndale<small>Estate Collective</small></span></div>
  <p class="footer-about">Lorem ipsum dolor sit amet, consectetur adipiscing elit, sed do eiusmod tempor...</p>

  <div class="fcol" style="left:332px">
    <h4>Site Map</h4>
    <ul><li>Home</li><li>About Us</li><li>Leasing</li><li>Buy</li><li>Sell</li><li>Our Team</li><li>Blog</li><li>Contact Us</li></ul>
  </div>

  <div class="fcol" style="left:613px">
    <h4>Contact Us</h4>
    <div class="contact-row"><svg width="20" height="22" fill="none" stroke="#333" stroke-width="1.3"><path d="M10 17s6-6 6-10A6 6 0 0 0 4 7c0 4 6 10 6 10z"/><circle cx="10" cy="7" r="2"/><path d="M3 21h14"/></svg><span>18/4 Wattlebird Parade,<br>Harwood, ACT, 2900</span></div>
    <div class="contact-row"><svg width="20" height="20" fill="none" stroke="#333" stroke-width="1.3"><path d="M4 2l4 4-2 2c1 3 3 5 6 6l2-2 4 4-3 3C8 18 2 12 1 5z"/></svg><span><b>02 6000 4821</b><br><b>02 6000 7390</b></span></div>
    <div class="contact-row"><svg width="20" height="16" fill="none" stroke="#333" stroke-width="1.3"><rect x="1" y="1" width="18" height="14"/><path d="M1 1l9 8 9-8"/></svg><span>info@ferndaleestatecollective.com.au</span></div>
  </div>

  <div class="fcol" style="left:889px">
    <h4>Follow On Us</h4>
    <div class="socials"><span class="on"><i></i></span><span><i></i></span><span><i></i></span><span><i></i></span></div>
  </div>

  <div class="legal">
    <span>2022© Ferndale Properties. All right reserved.</span>
    <nav><a>Privacy</a><a>Complaint Handling &amp; Dispute Resolution</a><a>Due Diligence Checklist</a></nav>
  </div>
</footer>

</body>
</html>
```